Marwick Family Chiropractic Stationary

The letterhead and business card must have our logo.
We would like to see the logo used in different ways ( It can be expanded upon in the stationary.)
Please use the the same or similar colors.
Must be eye catching and memorable.
Must be easy to read

Reason: The doctor has been too busy to make any final decisions. He would like to give himself a little more time.

Target Market(s)

Chiropractic Healthcare

Industry/Entity Type

Business

Requirements
Must have
• Dr. Leonard Marwick D.C.
Chiropractor

555-555-0183

417 Birchfield Road, Suite 2B
Larkfield 06091

drmarwick@marwickspine.example
www.marwickspine.example
www.facebook.com/MarwickFamilySpine
Should not have
• should not be difficult to read

```html
<!DOCTYPE html>
<html lang="en">
<head>
<meta charset="utf-8">
<title>Marwick Family Chiropractic – Business Cards</title>
<link rel="stylesheet" href="https://fonts.googleapis.com/css2?family=Montserrat:wght@700&family=Arimo:wght@400;700&display=swap">
<style>
  :root {
    --backdrop: #e9e6e1;
    --card-white: #ffffff;
    --card-black: #0a0a0a;
    --leaf-green: #2a9a48;
    --lime: #a6cf5c;
    --olive: #b0a637;
    --sun-yellow: #f7ec12;
    --ink: #2b2420;
    --ink-soft: #3a3a3a;
    --stone: #8d8a80;
    --faint: #e6e6e2;
  }
  * { box-sizing: border-box; margin: 0; padding: 0; }
  html, body { width: 1200px; height: 788px; overflow: hidden; background: var(--backdrop); }
  .sheet { position: relative; width: 1200px; height: 788px; }

  .card {
    position: absolute;
    width: 525px;
    height: 300px;
    border-radius: 20px;
    overflow: hidden;
    background: var(--card-white);
    font-family: "Arimo", Arial, sans-serif;
    color: var(--ink-soft);
  }
  .card--front  { left: 60px;  top: 79px; }
  .card--back-1 { left: 622px; top: 74px; }
  .card--back-2 { left: 54px;  top: 446px; }
  .card--back-3 { left: 622px; top: 446px; background: var(--card-black); }

  .swoosh { position: absolute; inset: 0; }

  .brand-mark {
    position: absolute;
    border-radius: 50%;
    background: var(--leaf-green);
  }
  .brand-name {
    position: absolute;
    font-family: "Montserrat", "Century Gothic", sans-serif;
    font-weight: 700;
    color: var(--leaf-green);
    text-align: center;
    line-height: 1;
    white-space: nowrap;
  }
  .brand-name span { display: block; }
  .brand-name .sub { color: var(--ink); }

  /* Front */
  .card--front .brand-mark { left: 62px; top: 26px; width: 88px; height: 88px; }
  .card--front .brand-name { left: 20px; top: 143px; width: 172px; }
  .card--front .brand-name .word { font-size: 27px; }
  .card--front .brand-name .sub  { font-size: 10.5px; margin-top: 6px; }

  .doctor { position: absolute; right: 17px; top: 47px; text-align: right; color: var(--ink); }
  .doctor__name  { font-weight: 700; font-size: 15px; letter-spacing: 0.3px; }
  .doctor__title { font-weight: 700; font-size: 11px; margin-top: 4px; }

  .contact { position: absolute; font-size: 11px; line-height: 17px; color: var(--ink-soft); white-space: nowrap; }
  .contact b { font-style: italic; font-weight: 700; }
  .contact--left  { left: 35px; top: 209px; }
  .contact--web   { left: 35px; top: 276px; }
  .contact--right { right: 17px; top: 237px; text-align: right; }
  .contact--right .fb { margin-bottom: 9px; }

  /* Back 1 */
  .card--back-1 .brand-mark { left: 208px; top: 26px; width: 108px; height: 108px; }
  .card--back-1 .brand-name { left: 0; width: 525px; top: 170px; }
  .card--back-1 .brand-name .word { font-size: 34px; }
  .card--back-1 .brand-name .sub  { font-size: 14px; margin-top: 7px; }

  .url { position: absolute; left: 0; width: 100%; text-align: center; font-size: 15px; color: var(--ink); }
  .card--back-1 .url { top: 261px; }

  /* Back 2 */
  .card--back-2 .faint-mark { position: absolute; left: 162px; top: 40px; width: 200px; height: 200px; border-radius: 50%; background: var(--faint); opacity: 0.6; }
  .card--back-2 .brand-name { left: 0; width: 525px; top: 96px; }
  .card--back-2 .brand-name .word { font-size: 62px; }
  .card--back-2 .brand-name .sub  { font-size: 25px; margin-top: 12px; }
  .card--back-2 .url { top: 261px; }

  /* Back 3 */
  .card--back-3 .brand-mark { left: 208px; top: 30px; width: 108px; height: 108px; background: var(--lime); }
  .card--back-3 .brand-name { left: 0; width: 525px; top: 172px; color: var(--lime); }
  .card--back-3 .brand-name .word { font-size: 32px; }
  .card--back-3 .brand-name .sub  { font-size: 14px; margin-top: 6px; color: var(--stone); }
  .card--back-3 .url { top: 261px; color: #ffffff; }
</style>
</head>
<body>
<main class="sheet">

  <section class="card card--front" aria-label="Business card front">
    <svg class="swoosh" width="525" height="300" viewBox="0 0 525 300" aria-hidden="true">
      <path d="M0 262 C260 268 420 215 525 108 L525 134 C420 240 260 274 0 268 Z" fill="var(--sun-yellow)"/>
      <path d="M0 276 C260 280 430 245 525 146 L525 300 L0 300 Z" fill="var(--olive)"/>
    </svg>
    <div class="brand-mark" aria-hidden="true"></div>
    <div class="brand-name"><span class="word">MARWICK</span><span class="sub">FAMILY CHIROPRACTIC</span></div>

    <div class="doctor">
      <div class="doctor__name">Dr. Leonard Marwick D.C.</div>
      <div class="doctor__title">Chiropractor</div>
    </div>

    <div class="contact contact--left">
      <div><b>ph</b> : 555-555-0183</div>
      <div><b>e</b> : drmarwick@marwickspine.example</div>
    </div>
    <div class="contact contact--web"><b>w</b> : www.marwickspine.example</div>
    <div class="contact contact--right">
      <div class="fb"><b>fb</b> : MarwickFamilySpine</div>
      <div>417 Birchfield Road</div>
      <div>Suite 2B, Larkfield 06091</div>
    </div>
  </section>

  <section class="card card--back-1" aria-label="Business card back, option one">
    <div class="brand-mark" aria-hidden="true"></div>
    <div class="brand-name"><span class="word">MARWICK</span><span class="sub">FAMILY CHIROPRACTIC</span></div>
    <div class="url">www.marwickspine.example</div>
  </section>

  <section class="card card--back-2" aria-label="Business card back, option two">
    <div class="faint-mark" aria-hidden="true"></div>
    <div class="brand-name"><span class="word">MARWICK</span><span class="sub">FAMILY CHIROPRACTIC</span></div>
    <div class="url">www.marwickspine.example</div>
  </section>

  <section class="card card--back-3" aria-label="Business card back, option three">
    <div class="brand-mark" aria-hidden="true"></div>
    <div class="brand-name"><span class="word">MARWICK</span><span class="sub">FAMILY CHIROPRACTIC</span></div>
    <div class="url">www.marwickspine.example</div>
  </section>

</main>
</body>
</html>
```